Honey apple cider vinegar label

organic food company need a contemporary honey apple cider vinegar and honey vinegar label, natural GMP logo HACCP LOgo
label detail height :140mm Width:80mm
ingredient: honey, apple cider vinegar and water, free from artificial color & preservative
Shelf Life: 3 years
Net weight 400ml
Storage : store in cool place , do not expose to sunlight
instruction for use: add 20ml to a full glass of water 3, times a days before meal, stop consuming if allergies happen
certification, GMP HACCP, Halal, natural product

Target Market(s)

health conscious group

Requirements
Must have
• modern feel, honey and apple picture

```html
<!DOCTYPE html>
<html lang="en">
<head>
<meta charset="utf-8">
<title>Honey Apple Cider Vinegar – Label Designs</title>
<link rel="stylesheet" href="https://fonts.googleapis.com/css2?family=Lobster&family=Open+Sans:wght@300;400;700&family=Playball&display=swap">
<style>
  :root{
    --olive:#7f8a52;
    --olive-band:#858c54;
    --sage-band:#728a58;
    --frame-inner:#d3d6c4;
    --title:#7b8450;
    --accent:#8f9550;
    --storage:#8b9a62;
    --ink:#4a4a3c;
    --brand:#2a1d3a;
    --star-lime:#d9e61a;
    --star-gold:#d8cc62;
    --star-green:#a3bb24;
    --paper:#ffffff;
  }
  html,body{margin:0;padding:0;width:1200px;height:1200px;overflow:hidden;background:var(--paper);}
  .sheet{display:block;width:1200px;height:1200px;}
  .sheet-border{fill:none;stroke:#6b6b6b;stroke-width:2;}
  .frame-outer{fill:var(--paper);stroke:var(--olive);stroke-width:11;}
  .frame-inner{fill:none;stroke:var(--frame-inner);stroke-width:8;}
  .tagline{font-family:'Playball',cursive;font-size:42px;fill:var(--accent);text-anchor:middle;}
  .product-name{font-family:'Lobster',cursive;font-size:72px;fill:var(--title);text-anchor:middle;}
  .info{font-family:'Open Sans',sans-serif;font-weight:300;font-size:24px;text-anchor:middle;fill:var(--body-ink,var(--ink));}
  .info-storage{fill:var(--storage-ink,var(--storage));}
  .brand-name{font-family:'Open Sans',sans-serif;font-weight:700;font-size:28px;fill:var(--brand);text-anchor:middle;}
  .brand-dot{fill:var(--olive);}
  .volume{font-family:'Lobster',cursive;font-size:92px;fill:var(--title);}
  .volume-unit{font-size:56px;}
  .shelf-life{font-family:'Open Sans',sans-serif;font-weight:400;font-size:25px;fill:var(--ink);text-anchor:middle;}
  .band-main{fill:var(--olive-band);}
  .band-storage{fill:var(--sage-band);}
  .badge-gmp{fill:#fff;stroke:var(--olive);stroke-width:4;}
  .badge-gmp-core{fill:var(--olive);}
  .badge-haccp{fill:#e8312f;stroke:#2f3c8f;stroke-width:3;}
  .badge-halal{fill:#fff;stroke:var(--olive);stroke-width:4;}
  .label-white{--body-ink:#ffffff;--storage-ink:#ffffff;}
</style>
</head>
<body>
<svg class="sheet" viewBox="0 0 1932 1932" xmlns="http://www.w3.org/2000/svg">
  <defs>
    <path id="label-shape" d="M300 475 Q288 482 292 497 Q345 970 292 1440 Q290 1456 306 1464 Q440 1530 500 1588 Q605 1665 710 1588 Q770 1530 904 1464 Q920 1456 918 1440 Q865 970 918 497 Q922 482 906 473 Q790 420 740 380 Q605 280 470 380 Q420 420 300 475 Z"/>
    <path id="label-inner-shape" d="M315 492 Q348 970 315 1430 Q450 1500 520 1565 Q605 1625 690 1565 Q760 1500 895 1430 Q862 970 895 492 Q780 440 730 400 Q605 312 480 400 Q430 440 315 492 Z"/>
    <clipPath id="label-clip"><use href="#label-inner-shape" transform="translate(-10 0) scale(1.016 1)"/></clipPath>
    <polygon id="star" points="0,-20 5.9,-8.1 19,-6.2 9.5,3.1 11.8,16.2 0,10 -11.8,16.2 -9.5,3.1 -19,-6.2 -5.9,-8.1"/>
    <linearGradient id="honey-apple" x1="0" y1="0" x2="1" y2="1">
      <stop offset="0" stop-color="#e6cf9e"/>
      <stop offset="0.45" stop-color="#f5a716"/>
      <stop offset="1" stop-color="#c9262a"/>
    </linearGradient>

    <g id="label-frame">
      <use href="#label-shape" class="frame-outer"/>
      <use href="#label-inner-shape" class="frame-inner"/>
    </g>

    <g id="label-content">
      <g class="rating">
        <use href="#star" transform="translate(513 422) scale(0.8)" fill="var(--star-lime)"/>
        <use href="#star" transform="translate(555 410) scale(0.95)" fill="var(--star-gold)"/>
        <use href="#star" transform="translate(605 396) scale(1.2)" fill="var(--star-green)"/>
        <use href="#star" transform="translate(655 410) scale(0.95)" fill="var(--star-gold)"/>
        <use href="#star" transform="translate(697 422) scale(0.8)" fill="var(--star-lime)"/>
      </g>
      <rect class="hero-illustration" role="img" aria-label="Illustration of a honey jar with cloth lid, daisy and a red apple" x="445" y="455" width="335" height="340" rx="120" fill="url(#honey-apple)"/>
      <text class="tagline" x="604" y="843" textLength="272" lengthAdjust="spacingAndGlyphs">organic &amp; natural</text>
      <text class="product-name" x="598" y="925" textLength="420" lengthAdjust="spacingAndGlyphs">Honey Apple Cider</text>
      <text class="product-name" x="592" y="1003" textLength="220" lengthAdjust="spacingAndGlyphs">Vinegar</text>
      <g class="ingredients">
        <text class="info" x="606" y="1055">ingredient: honey, apple cider vinegar and</text>
        <text class="info" x="606" y="1088">water, free from artificial color &amp;</text>
        <text class="info" x="606" y="1120">preservative</text>
      </g>
      <g class="storage">
        <text class="info info-storage" x="606" y="1159">store in cool place ,</text>
        <text class="info info-storage" x="606" y="1191">do not expose to sunlight</text>
      </g>
      <g class="directions">
        <text class="info" x="606" y="1231">instruction for use:</text>
        <text class="info" x="606" y="1264">add 20ml to a full glass of water</text>
        <text class="info" x="606" y="1296">3 times a days before meal,</text>
        <text class="info" x="606" y="1329">stop consuming if allergies happen</text>
      </g>
      <g class="brand">
        <circle class="brand-dot" cx="420" cy="1388" r="24"/>
        <text class="brand-name" x="420" y="1443">Orchavia</text>
      </g>
      <text class="volume" x="500" y="1422">400<tspan class="volume-unit" dx="8">ml</tspan></text>
      <text class="shelf-life" x="607" y="1457">Shelf Life: 3 years</text>
      <g class="certifications">
        <circle class="badge-gmp" cx="505" cy="1517" r="47"/>
        <circle class="badge-gmp-core" cx="505" cy="1517" r="28"/>
        <circle class="badge-haccp" cx="607" cy="1517" r="47"/>
        <polygon class="badge-halal" points="707,1468 724,1483 748,1483 748,1507 760,1517 748,1527 748,1551 724,1551 707,1566 690,1551 666,1551 666,1527 654,1517 666,1507 666,1483 690,1483"/>
      </g>
    </g>
  </defs>

  <rect class="sheet-border" x="1" y="1" width="1930" height="1930"/>

  <g class="label label-plain">
    <use href="#label-frame"/>
    <use href="#label-content"/>
  </g>

  <g class="label label-banded label-white" transform="translate(723 0)">
    <use href="#label-frame"/>
    <g clip-path="url(#label-clip)">
      <rect class="band-main" x="280" y="1022" width="650" height="320"/>
      <rect class="band-storage" x="280" y="1133" width="650" height="71"/>
    </g>
    <use href="#label-content"/>
  </g>
</svg>
</body>
</html>
```